Website Development for vaultmerrow.com.au

Build a new Wordpress/Responsive website for vaultmerrow.com.au

Target Market(s)

Compliance Managers, Risk Managers, Information Security and Cyber Security Professionals, Chief Data/Digital Officers, Chief Operating/Financial Officers, Business Continuity Professionals, Disaster Recovery Planners, Small Business Owners, Local/Federal Government entities

Industry/Entity Type

Data Service

Coding

Coded - Design and coding required

Number of Pages Required

5+ page

Font styles to use
Sans Serif

Colors

Designer to choose colors to be used in the design.

Requirements
Must have
• 1. Site Structure: Home Page plus the following chapter-pages for a) Services b) About c) Resources d) Blog e) Contact Us
• 2. Prefer site to built on wordpress and we can purchase a theme if needed (we currently use Kelp9 for other sites)
• 3. Blog needs to be wordpress based
• 4. We will host the site ourselves on our own servers
• 5. Responsive Design
Nice to have
• 1. Livechat capability/interface
• 2. Capability for marketing automation integration (such as hubspot, marketo, infusionsoft etc)
• 3. Capability for CRM integration (Salesforce)

```html
<!DOCTYPE html>
<html lang="en">
<head>
<meta charset="utf-8">
<title>Vault Merrow</title>
<link href="https://fonts.googleapis.com/css2?family=Roboto:wght@400;500;700;900&display=swap" rel="stylesheet">
<style>
:root{
  --red:#e31e26;
  --red-dark:#c3161d;
  --navy:#0d1540;
  --ink:#222;
  --text:#444;
  --grey-bg:#f1f1f1;
  --footer:#1f1f1f;
  --white:#fff;
}
*{box-sizing:border-box;margin:0;padding:0}
html,body{width:1200px;height:3422px;overflow:hidden}
body{font-family:'Roboto',sans-serif;color:var(--ink);background:var(--white);position:relative}
.abs{position:absolute}
.btn{position:absolute;display:flex;align-items:center;justify-content:center;background:var(--red);color:var(--white);font-weight:700;font-size:19px;width:192px;height:55px;border-radius:4px 18px 4px 18px;text-decoration:none}
.wave{position:absolute;left:0;width:1200px;height:40px}
.chev{position:absolute;left:588px;width:24px;height:24px}
.body-text{font-size:15.5px;line-height:29px;color:var(--text);text-align:justify}

/* header */
.site-header{position:absolute;top:0;left:0;width:1200px;height:103px;background:var(--white);z-index:3}
.logo-blob{position:absolute;top:0;left:0;z-index:4}
.brand{position:absolute;left:112px;top:62px;z-index:5;display:flex;align-items:center;gap:14px;color:var(--red);font-weight:700;font-size:44px;letter-spacing:1px}
.brand .dot{width:40px;height:40px;border-radius:50%;background:var(--red)}
.phone{position:absolute;left:893px;top:10px;display:flex;align-items:center;gap:16px;font-size:20px;color:var(--ink)}
.phone .ic{width:40px;height:40px;border-radius:50%;background:var(--red);display:flex;align-items:center;justify-content:center}
.main-nav{position:absolute;top:63px;left:627px;display:flex;gap:30px;font-size:16px;color:#333}
.main-nav .active{color:var(--red)}

/* hero */
.hero{position:absolute;top:103px;left:0;width:1200px;height:575px;background:linear-gradient(100deg,#0a0f3a 0%,#1a1f66 45%,#5a2a40 70%,#c0391a 100%)}
.hero-title{position:absolute;left:110px;top:292px;font-size:70px;font-weight:900;color:var(--white)}
.hero-sub{position:absolute;left:114px;top:392px;font-size:20px;line-height:32px;color:var(--white);font-weight:500;width:560px}
.dots span{position:absolute;left:1130px;width:14px;height:14px;border-radius:50%;background:var(--white)}

/* about */
.about-photo{position:absolute;left:135px;top:783px;width:310px;height:310px;border-radius:50%;background:radial-gradient(circle,#2b3d6e 0%,#0e1834 70%,#0a0f22 100%)}
.eyebrow{position:absolute;left:511px;top:780px;font-size:25px;color:#333}
.sec-title{font-weight:700;color:var(--red);font-size:44px}

/* services */
.services{position:absolute;top:1243px;left:0;width:1200px;height:616px;background:linear-gradient(180deg,#e5242b 0%,#dc1f27 60%,#e02a30 100%)}
.services h2{position:absolute;top:80px;width:1200px;text-align:center;color:var(--white);font-size:42px;font-weight:700}
.svc{position:absolute;top:185px;width:290px;text-align:center;color:var(--white)}
.svc .ring{width:114px;height:114px;border:3px solid var(--white);border-radius:50%;margin:0 auto}
.svc h3{font-size:22px;font-weight:700;margin-top:38px}
.svc p{font-size:14px;line-height:27px;margin-top:14px}
.svc .more{margin:16px auto 0;width:24px;height:24px}
.arrow{position:absolute;top:346px;width:46px;height:46px;border-radius:50%;background:var(--white);display:flex;align-items:center;justify-content:center}

/* resources */
.res-photo{position:absolute;left:664px;top:1953px;width:424px;height:322px;background:linear-gradient(180deg,#d8dde3 0%,#8fa4b6 45%,#6e6f6a 100%);z-index:2}
.res-frame{position:absolute;left:680px;top:1968px;width:424px;height:322px;background:var(--red)}

/* blog */
.blog{position:absolute;top:2373px;left:0;width:1200px;height:666px;background:var(--grey-bg)}
.blog h2{position:absolute;top:70px;width:1200px;text-align:center}
.post{position:absolute;top:171px;width:308px}
.post .thumb{width:308px;height:166px}
.post .date{position:absolute;top:194px;left:0;width:38px;height:42px;background:var(--white);border:1px solid #ddd;font-size:11px;text-align:center;line-height:15px;padding-top:5px;color:#555}
.post h3{position:absolute;top:192px;left:56px;font-size:20px;font-weight:500;line-height:24px;color:var(--ink)}
.post p{position:absolute;top:256px;font-size:15px;line-height:27px;color:var(--text)}
.post .btn{top:360px;left:0}

/* footer */
.site-footer{position:absolute;top:3039px;left:0;width:1200px;height:383px;background:var(--footer);color:var(--white)}
.foot-brand{position:absolute;left:150px;top:100px;display:flex;align-items:center;gap:12px;font-size:40px;font-weight:700;letter-spacing:1px}
.foot-brand .dot{width:36px;height:36px;border-radius:50%;background:var(--white)}
.social{position:absolute;left:205px;top:218px;display:flex;gap:11px}
.social span{width:25px;height:25px;border:1.5px solid var(--white);border-radius:50%}
.foot-col h4{position:absolute;font-size:21px;font-weight:700}
.links{position:absolute;list-style:none;font-size:14px;font-weight:500}
.links li{height:29px;padding-left:18px;position:relative}
.links li::before{content:"›";position:absolute;left:2px;top:-2px;color:#aaa}
.contact-line{position:absolute;left:846px;display:flex;gap:18px;font-size:14px;font-weight:500;line-height:24px}
.foot-bar{position:absolute;left:112px;top:319px;width:976px;height:1px;background:#3a3a3a}
.copy{position:absolute;top:339px;font-size:13px;font-weight:500}
</style>
</head>
<body>

<!-- header -->
<header class="site-header">
  <div class="phone">
    <span class="ic"><svg width="20" height="20" viewBox="0 0 24 24"><path fill="#fff" d="M6.6 10.8a15 15 0 006.6 6.6l2.2-2.2c.3-.3.7-.4 1-.2 1.1.4 2.3.6 3.6.6.6 0 1 .4 1 1V20c0 .6-.4 1-1 1A17 17 0 013 4c0-.6.4-1 1-1h3.5c.6 0 1 .4 1 1 0 1.3.2 2.5.6 3.6.1.3 0 .7-.2 1z"/></svg></span>
    (555) 014 3210
  </div>
  <nav class="main-nav">
    <span class="active">Home</span><span>About</span><span>Services</span><span>Resources</span><span>Blog</span><span>Contact Us</span>
  </nav>
</header>
<svg class="logo-blob" width="490" height="210" viewBox="0 0 490 210"><path fill="#fff" d="M0 0H490C470 110 380 205 230 205C110 205 40 170 0 140Z"/></svg>
<div class="brand"><span class="dot"></span>VAULT MERROW</div>

<!-- hero -->
<section class="hero" role="img" aria-label="Glowing padlock over a dark circuit board background">
  <div class="hero-title" style="top:190px">Vault Merrow</div>
  <p class="hero-sub" style="top:290px">Lorem ipsum dolor sit amet, consectetur adipiscing elit, sed do eiusmod tempor incididunt ut labore</p>
  <a class="btn" style="left:112px;top:369px">Read More</a>
  <div class="dots">
    <span style="top:262px;width:24px;height:24px;left:1127px;background:none;border:3px solid #fff"></span>
    <span style="top:302px"></span>
    <span style="top:326px"></span>
  </div>
</section>
<svg class="wave" style="top:638px" viewBox="0 0 1200 40"><path fill="#fff" d="M0 40C420 40 480 0 600 0S780 40 1200 40Z"/></svg>
<svg class="chev" style="top:660px" viewBox="0 0 24 24"><circle cx="12" cy="12" r="10" fill="none" stroke="#333" stroke-width="1.5"/><path d="M7.5 10l4.5 4.5 4.5-4.5" fill="none" stroke="#333" stroke-width="1.5"/></svg>

<!-- about -->
<section class="about">
  <div class="about-photo" role="img" aria-label="Circular photo with a shield emblem over a data network"></div>
  <div class="eyebrow">About Us</div>
  <h2 class="sec-title abs" style="left:510px;top:810px">Vault Merrow</h2>
  <p class="body-text abs" style="left:511px;top:872px;width:546px">Lorem ipsum dolor sit amet, consectetur adipiscing elit, sed do eiusmod tempor incididunt ut labore et dolore magna aliqua. Ut enim ad minim veniam, quis nostrud exercitation ullamco laboris nisi ut aliquip ex ea commodo consequat. Duis aute irure dolor in reprehenderit in voluptate velit esse cillum dolore eu fugiat nulla pariatur. Excepteur sint occaecat cupidatat non proident, sunt in culpa qui officia deserunt mollit anim id est laborum.</p>
  <a class="btn" style="left:511px;top:1068px">Read More</a>
</section>

<!-- services -->
<section class="services" role="img" aria-label="Red tinted background of padlocks and a computer screen">
  <h2>Our Services</h2>
  <div class="svc" style="left:136px">
    <div class="ring"></div>
    <h3>Information Security</h3>
    <p>Sed ut perspiciatis unde omnis iste natus error sit voluptatem accusantium doloremque laudantium, totam rem aperiam, eaque ipsa quae</p>
    <svg class="more" viewBox="0 0 24 24"><circle cx="12" cy="12" r="10" fill="none" stroke="#fff" stroke-width="1.5"/><path d="M7.5 10l4.5 4.5 4.5-4.5" fill="none" stroke="#fff" stroke-width="1.5"/></svg>
  </div>
  <div class="svc" style="left:455px">
    <div class="ring"></div>
    <h3>Cyber Security</h3>
    <p>Sed ut perspiciatis unde omnis iste natus error sit voluptatem accusantium doloremque laudantium, totam rem aperiam, eaque ipsa quae</p>
    <svg class="more" viewBox="0 0 24 24"><circle cx="12" cy="12" r="10" fill="none" stroke="#fff" stroke-width="1.5"/><path d="M7.5 10l4.5 4.5 4.5-4.5" fill="none" stroke="#fff" stroke-width="1.5"/></svg>
  </div>
  <div class="svc" style="left:774px">
    <div class="ring"></div>
    <h3>Compliance Management</h3>
    <p>Sed ut perspiciatis unde omnis iste natus error sit voluptatem accusantium doloremque laudantium, totam rem aperiam, eaque ipsa quae</p>
    <svg class="more" viewBox="0 0 24 24"><circle cx="12" cy="12" r="10" fill="none" stroke="#fff" stroke-width="1.5"/><path d="M7.5 10l4.5 4.5 4.5-4.5" fill="none" stroke="#fff" stroke-width="1.5"/></svg>
  </div>
  <span class="arrow" style="left:45px"><svg width="14" height="14" viewBox="0 0 14 14"><path d="M9 2L4 7l5 5" fill="none" stroke="#333" stroke-width="2"/></svg></span>
  <span class="arrow" style="left:1107px"><svg width="14" height="14" viewBox="0 0 14 14"><path d="M5 2l5 5-5 5" fill="none" stroke="#333" stroke-width="2"/></svg></span>
</section>
<svg class="wave" style="top:1203px" viewBox="0 0 1200 40"><path fill="#e5242b" d="M0 40C420 40 480 0 600 0S780 40 1200 40Z"/></svg>
<svg class="chev" style="top:1236px" viewBox="0 0 24 24"><circle cx="12" cy="12" r="10" fill="none" stroke="#333" stroke-width="1.5"/><path d="M7.5 10l4.5 4.5 4.5-4.5" fill="none" stroke="#333" stroke-width="1.5"/></svg>
<svg class="wave" style="top:1819px" viewBox="0 0 1200 40"><path fill="#fff" d="M0 40C420 40 480 0 600 0S780 40 1200 40Z"/></svg>
<svg class="chev" style="top:1843px" viewBox="0 0 24 24"><circle cx="12" cy="12" r="10" fill="none" stroke="#333" stroke-width="1.5"/><path d="M7.5 10l4.5 4.5 4.5-4.5" fill="none" stroke="#333" stroke-width="1.5"/></svg>

<!-- resources -->
<section class="resources">
  <h2 class="sec-title abs" style="left:110px;top:1946px">Resources</h2>
  <p class="body-text abs" style="left:112px;top:2016px;width:493px">Lorem ipsum dolor sit amet, consectetur adipiscing elit, sed do eiusmod tempor incididunt ut labore et dolore magna aliqua. Ut enim ad minim veniam, quis nostrud exercitation ullamco laboris nisi ut aliquip ex ea commodo consequat. Duis aute irure dolor in reprehenderit in voluptate velit esse cillum dolore eu fugiat nulla pariatur. Excepteur sint occaecat cupidatat non proident, sunt in culpa qui officia deserunt mollit anim id est laborum. Lorem ipsum dolor sit amet</p>
  <a class="btn" style="left:112px;top:2238px">Read More</a>
  <div class="res-frame"></div>
  <div class="res-photo" role="img" aria-label="Volunteers in blue shirts unloading boxes under a tent"></div>
</section>

<!-- blog -->
<section class="blog">
  <h2 class="sec-title">Our Blog</h2>
  <article class="post" style="left:112px">
    <div class="thumb" role="img" aria-label="Hand placing a compliance block on a stack of wooden blocks" style="background:linear-gradient(135deg,#5d6b4a,#9a8a5c 60%,#3c4330)"></div>
    <div class="date">29<br>Jan</div>
    <h3>At vero eos et accusamus et iusto odio</h3>
    <p>Lorem ipsum dolor sit amet, consectetur adipisicing elit, sed do eiusmod tempor incididunt ut labore et dolore.</p>
    <a class="btn">Read More</a>
  </article>
  <article class="post" style="left:445px">
    <div class="thumb" role="img" aria-label="Row of wooden blocks printed with policy words" style="background:linear-gradient(180deg,#3a3530,#8a7a66 55%,#c9b89e)"></div>
    <div class="date">29<br>Jan</div>
    <h3>At vero eos et accusamus et iusto odio</h3>
    <p>Lorem ipsum dolor sit amet, consectetur adipisicing elit, sed do eiusmod tempor incididunt ut labore et dolore.</p>
    <a class="btn">Read More</a>
  </article>
  <article class="post" style="left:778px">
    <div class="thumb" role="img" aria-label="Hand touching a glowing padlock among security icons" style="background:linear-gradient(135deg,#0e1a2e,#2a4866 55%,#0b1422)"></div>
    <div class="date">29<br>Jan</div>
    <h3>At vero eos et accusamus et iusto odio</h3>
    <p>Lorem ipsum dolor sit amet, consectetur adipisicing elit, sed do eiusmod tempor incididunt ut labore et dolore.</p>
    <a class="btn">Read More</a>
  </article>
</section>
<svg class="wave" style="top:2333px" viewBox="0 0 1200 40"><path fill="#f1f1f1" d="M0 40C420 40 480 0 600 0S780 40 1200 40Z"/></svg>
<svg class="chev" style="top:2374px" viewBox="0 0 24 24"><circle cx="12" cy="12" r="10" fill="none" stroke="#333" stroke-width="1.5"/><path d="M7.5 10l4.5 4.5 4.5-4.5" fill="none" stroke="#333" stroke-width="1.5"/></svg>

<!-- footer -->
<footer class="site-footer">
  <div class="foot-brand"><span class="dot"></span>VAULT MERROW</div>
  <div class="social"><span></span><span></span><span></span><span></span></div>
  <div class="foot-col">
    <h4 style="left:511px;top:66px">Quick Links</h4>
    <ul class="links" style="left:515px;top:119px">
      <li>Home</li><li>About</li><li>Services</li><li>Resources</li><li>Blog</li>
    </ul>
    <ul class="links" style="left:648px;top:119px">
      <li>Contact Us</li><li>Login</li><li>Privacy Policy</li>
    </ul>
  </div>
  <div class="foot-col">
    <h4 style="left:846px;top:66px">Contact Us</h4>
    <div class="contact-line" style="top:115px">
      <svg width="20" height="22" viewBox="0 0 24 24"><path fill="#fff" d="M12 2a7 7 0 00-7 7c0 5 7 13 7 13s7-8 7-13a7 7 0 00-7-7zm0 9.5A2.5 2.5 0 1112 6a2.5 2.5 0 010 5.5z"/></svg>
      <span>18 Harlow Lane 2/7<br>Brookvale City, US</span>
    </div>
    <div class="contact-line" style="top:184px">
      <svg width="20" height="20" viewBox="0 0 24 24"><path fill="none" stroke="#fff" stroke-width="1.6" d="M6.6 10.8a15 15 0 006.6 6.6l2.2-2.2c.3-.3.7-.4 1-.2 1.1.4 2.3.6 3.6.6.6 0 1 .4 1 1V20c0 .6-.4 1-1 1A17 17 0 013 4c0-.6.4-1 1-1h3.5c.6 0 1 .4 1 1 0 1.3.2 2.5.6 3.6.1.3 0 .7-.2 1z"/></svg>
      <span>1 (800) 555-0142</span>
    </div>
    <div class="contact-line" style="top:227px">
      <svg width="20" height="20" viewBox="0 0 24 24"><rect x="2.5" y="5" width="19" height="14" fill="none" stroke="#fff" stroke-width="1.6"/><path d="M2.5 5l9.5 8 9.5-8" fill="none" stroke="#fff" stroke-width="1.6"/></svg>
      <span>info@vaultmerrow.com</span>
    </div>
  </div>
  <div class="foot-bar"></div>
  <div class="copy" style="left:112px">© Copyrights 2019 | All Rights Reserved</div>
  <div class="copy" style="left:747px">Terms &amp; Conditions</div>
  <div class="copy" style="left:902px">Privacy Policy</div>
  <div class="copy" style="left:1013px">Contact Us</div>
</footer>
<svg class="wave" style="top:2999px" viewBox="0 0 1200 40"><path fill="#1f1f1f" d="M0 40C420 40 480 0 600 0S780 40 1200 40Z"/></svg>
<svg class="chev" style="top:3038px" viewBox="0 0 24 24"><circle cx="12" cy="12" r="10" fill="none" stroke="#fff" stroke-width="1.5"/><path d="M7.5 10l4.5 4.5 4.5-4.5" fill="none" stroke="#fff" stroke-width="1.5"/></svg>

</body>
</html>
```